Bold, Modern, Clean "Kestrelwaymassage.com" website

Why we stand out?
We are a male and female mobile massage team. Our names are Paul and Lina. 
Kestrel Way is a Seattle based mobile massage service. Our massage is offered to the community with a goal of facilitating balance within each individual. We specialize in integrated Pain management, and sports/medical massage therapy. Every client's first assessment is attended by our male and female massage therapist team. Depending on the goals identified for an individual determines which therapist will be assigned to provide treatment, if not both.

Our passion...
Here at Kestrel Way, we have a great passion for Postural Resoration and how it is integrated into an individual's Massage treatment. We pride ourselves in being natural facilitators of healing, which takes the ego of the therapist out of the client's healing process. We strive to deliver the best massage possible by including modalities such as Neuromuscular, Myofascial release, spontaneous muscle release, postural restoration, orthopedic, and medical massage.

Our education...

We are both Graduates of Venmora, school of massage therapy. We have continuing education in medical massage, myofacial release, trigger point therapy, postural restoration, anatomy, and spontaneous muscle release. Lina is also a Certified Yoga Instructor, which amplifies her experience with flexibility and strength as it pertains to each individual. Paul's passion is Massage, stretching, and strength training to encourage postural restoration and realignment.

Our rates-

Our rates are $75/ 60 minutes, $95/ 90 minutes, and $120/ 120 minutes.

Education-
Both Lina and I worked as behavioral health professionals that specialized in life skills mentoring for youth who had experienced different types of trauma. This led us both to want to help others in a different environment, where individuals can be empowered to take responsibility over their own healing. To us, massage is a type of manipulation physical therapy, that encourages healing on many levels.

Advice to any massage client-
The most important thing to 'us', as Licenced providers is to get you on to our table to show you our skills. But a good therapist never forgets that it's not about what we do for you, but what we can facilitate for you. Your health and healing has nothing to do with us. It is yours, not ours. Identify what your goals are with any Therapist, and know what the end looks like. Progress should be tangible, such as range of motion, and decreased pain.

Lina and Paul at Kestrel Way are awesome! I recently had open heart surgery, and Lina worked on me to increase my range of motion while helping with the pinched nerve from my arm being in the same position for so long during my surgery. My wife drives a lot for work, and Paul has helped decrease her neck and lower back pain immensely. They are seriously the best therapists I have ever worked with. I would recommend them to anyone who needs anything from stress relief to a medical massage treatment. They are professional, up beat, easy going, and always on time. And, I love that they meet us where ever we like! We did a staycation recently, where they came to our hotel to give us relaxation massages. Although usually they come to our home, where we focus on pain related issues. We will continue to work with them for a long, long time.

Target Market(s)

Mobile massage therapy clients

Industry/Entity Type

Massage Therapy

Coding

Coded - Design and coding required

Number of Pages Required

1 page

Font styles to use
Serif
Sans Serif

Requirements
Must have
• Please add or remove any information that would help the presentation of our website. Our logo is posted below, please include into the website.
• Please include a contact field that includes, kestrelwaymassage@fernmail.net,
• (206) 555-0148
• We have also included our own stock photos, as well as a photo of Paul and Lina. Please include a cropped photo of both massage therapists.

```html
<!DOCTYPE html>
<html lang="en">
<head>
<meta charset="utf-8">
<title>Kestrel Way – Mobile Massage</title>
<link rel="stylesheet" href="https://fonts.googleapis.com/css2?family=Raleway:wght@300;400;600;700&family=Arimo:wght@400&display=swap">
<style>
:root{
  --teal:#06f0cc;
  --teal-deep:#07d9b9;
  --ink:#1d1d1d;
  --grey-text:#555555;
  --band-light:#f3f3f3;
  --footer:#343434;
  --field:#6a6a6a;
  --field-line:#8a8a8a;
  --icon-ring:#4a4a4a;
  --icon-light:#b4b4b4;
  --icon-mid:#8f8f8f;
  --icon-dark:#555555;
  --icon-deep:#3e3e3e;
  --navy:#1b2a8c;
  --logo-blue:#1560c9;
  --white:#ffffff;
}
*{margin:0;padding:0;box-sizing:border-box}
html,body{width:1200px;height:2667px;overflow:hidden;background:var(--white)}
body{position:relative;font-family:"Raleway",sans-serif;color:var(--ink)}
.abs{position:absolute}
.photo{position:absolute}

/* hero */
.hero{position:absolute;left:0;top:0;width:1200px;height:654px;
  background:radial-gradient(ellipse at 45% 45%,#5b4634 0%,#3a2b20 45%,#1f1711 100%)}
.nav a{position:absolute;top:73px;font-weight:700;font-size:16px;color:var(--white);text-decoration:none;letter-spacing:.3px}
.nav a.is-active{color:var(--teal)}
.brand{position:absolute;left:530px;top:14px;width:140px;height:140px;border-radius:50%;
  background:var(--logo-blue);display:flex;align-items:center;justify-content:center;
  font-weight:700;font-size:24px;line-height:1.05;color:var(--white);text-align:center}
.hero-title{position:absolute;left:0;width:1200px;top:290px;text-align:center;color:var(--white);font-size:58px;line-height:64px}
.hero-title strong{font-weight:700;display:block}
.hero-title span{font-weight:400;display:block}

/* welcome */
.welcome{position:absolute;left:0;top:658px;width:1200px;height:311px;background:var(--band-light)}
.welcome h2{position:absolute;left:0;width:1200px;top:48px;text-align:center;font-weight:400;font-size:36px}
.welcome p{position:absolute;left:308px;width:584px;top:112px;text-align:center;font-family:"Arimo",sans-serif;font-size:15px;line-height:23px;color:var(--grey-text)}
.btn-outline{position:absolute;border:2px solid #555;border-radius:26px;display:flex;align-items:center;justify-content:center;font-size:16px;letter-spacing:.5px;background:transparent}
.read-more{left:523px;top:206px;width:154px;height:50px;color:#444}

/* services */
.services-title{position:absolute;left:0;width:1200px;top:1140px;text-align:center;font-size:36px;font-weight:400}
.service{position:absolute;width:0;height:0}
.service-ring{position:absolute;left:-70px;top:-70px;width:140px;height:140px;border-radius:50%;border:3px solid var(--icon-ring);background:var(--white);padding:5px}
.service-ring i{display:block;width:100%;height:100%;border-radius:50%;border:2px solid var(--icon-ring)}
.tone-neuro i{background:radial-gradient(circle at 30% 30%,var(--icon-deep) 0%,var(--icon-dark) 40%,var(--teal-deep) 62%,#10c7a8 100%)}
.tone-myo i{background:radial-gradient(circle at 50% 40%,var(--icon-light) 0%,var(--icon-mid) 60%,var(--icon-dark) 100%)}
.tone-spont i{background:radial-gradient(ellipse at 50% 60%,var(--icon-light) 0%,#9c9c9c 55%,var(--icon-dark) 100%)}
.tone-postural i{background:radial-gradient(ellipse at 50% 65%,var(--icon-light) 0%,var(--icon-mid) 55%,var(--icon-dark) 100%)}
.tone-ortho i{background:radial-gradient(circle at 55% 45%,#9a9a9a 0%,var(--icon-dark) 45%,var(--icon-deep) 100%)}
.tone-medical i{background:radial-gradient(ellipse at 50% 50%,#cfcfcf 0%,#8a8a8a 35%,var(--icon-dark) 70%,var(--icon-deep) 100%)}
.service-label{position:absolute;left:-110px;width:220px;text-align:center;font-size:18px;line-height:25px;color:#333}

/* testimonial */
.reviews{position:absolute;left:0;top:1563px;width:1200px;height:414px;
  background:linear-gradient(90deg,#2a2826 0%,#3d3935 45%,#2b2927 100%)}
.reviews h2{position:absolute;left:0;width:1200px;top:48px;text-align:center;font-weight:400;font-size:36px;color:var(--white)}
.reviews h2 em{font-style:normal;color:var(--teal)}
.stars{position:absolute;left:556px;top:112px}
.avatar{position:absolute;left:475px;top:171px;width:88px;height:88px;border-radius:50%;border:3px solid var(--white);background:#b9a48f}
.reviewer{position:absolute;left:590px;top:185px;font-size:19px;color:var(--teal)}
.review-date{position:absolute;left:590px;top:216px;font-family:"Arimo",sans-serif;font-size:15px;color:var(--white)}
.arrow{position:absolute;top:203px}
.quote{position:absolute;left:215px;width:770px;top:276px;text-align:center;font-family:"Arimo",sans-serif;font-size:15px;line-height:23px;color:var(--white)}

/* call band */
.call{position:absolute;left:0;top:1977px;width:1200px;height:169px;background:var(--white)}
.call-number{position:absolute;left:178px;top:52px;font-weight:600;font-size:49px;color:#2b2b2b}
.call-btn{left:638px;top:57px;width:155px;height:50px;border-color:var(--navy);color:var(--navy);font-size:15px}
.device{position:absolute;left:850px;top:1920px;width:320px;height:215px;
  clip-path:polygon(18px 36px,110px 6px,314px 142px,226px 213px);
  background:linear-gradient(150deg,#161616 0%,#2a2a2a 14%,#3561a8 26%,#e3e9f2 44%,#f4f6fa 62%,#3a6fb8 78%,#1b1b1b 90%,#0f0f0f 100%)}

/* footer */
.footer{position:absolute;left:0;top:2146px;width:1200px;height:521px;background:var(--footer)}
.contact-line{position:absolute;left:192px;display:flex;align-items:center;gap:16px;font-family:"Arimo",sans-serif;font-size:17px;color:#e6e6e6}
.contact-title{position:absolute;left:251px;top:190px;font-weight:400;font-size:38px;color:var(--teal);letter-spacing:.5px}
.field{position:absolute;left:521px;width:364px;background:var(--field);border:1px solid var(--field-line);font-family:"Arimo",sans-serif;font-size:13px;color:#d8d8d8;padding:14px 12px}
.send{position:absolute;left:761px;top:343px;width:124px;height:50px;border:2px solid #e0e0e0;color:var(--white);display:flex;align-items:center;justify-content:center;font-size:20px}
.footer-brand{position:absolute;left:967px;top:63px;width:104px;height:104px;border-radius:50%;background:#e9e9e9;display:flex;align-items:center;justify-content:center;text-align:center;font-weight:700;font-size:17px;line-height:1.05;color:#333}
.social{position:absolute;top:208px;width:52px;height:52px;border:2px solid var(--teal)}
.social.filled{background:var(--teal)}
.copyright{position:absolute;left:651px;top:479px;font-weight:600;font-size:14px;color:var(--white)}
.copyright span{color:var(--teal)}
</style>
</head>
<body>

<header class="hero">
  <div class="photo" role="img" aria-label="Client receiving a back massage on a spa table with candles and flowers" style="inset:0"></div>
  <nav class="nav">
    <a class="is-active" style="left:197px" href="#">HOME</a>
    <a style="left:286px" href="#">ABOUT</a>
    <a style="left:380px" href="#">SERVICES</a>
    <a style="left:738px" href="#">PRICING</a>
    <a style="left:841px" href="#">BLOG</a>
    <a style="left:924px" href="#">CONTACT</a>
  </nav>
  <div class="brand">Kestrel<br>Way</div>
  <h1 class="hero-title"><strong>Health, Medical,</strong><span>Pharmaceuticals</span></h1>
</header>

<section class="welcome">
  <h2>Welcome To KESTREL WAY</h2>
  <p>Lorem Ipsum is simply dummy text of the printing and typesetting industry. Lorem Ipsum has been the industry's standard dummy text ever since the 1500s, when an unknown printer took a galley of type and scrambled it to.</p>
  <div class="btn-outline read-more">READ MORE</div>
</section>
<div class="photo" role="img" aria-label="Cropped photo of therapist Lina" style="left:0;top:658px;width:310px;height:412px;background:linear-gradient(160deg,#6b5a4e 0%,#8a8f95 55%,#5c6168 100%)"></div>
<div class="photo" role="img" aria-label="Cropped photo of therapist Paul crouching in sportswear" style="left:880px;top:666px;width:294px;height:384px;background:linear-gradient(180deg,#caa58a 0%,#2f56b5 35%,#1e1e1e 75%,#3a3a3a 100%);clip-path:polygon(20% 0,70% 0,100% 45%,100% 100%,8% 100%,0 55%)"></div>

<svg class="abs" style="left:0;top:1000px" width="1200" height="490" viewBox="0 1000 1200 490" aria-hidden="true">
  <polygon points="0,1072 284,1013 1200,1218 1200,1476 0,1351" fill="var(--teal)"/>
  <rect x="480" y="1064" width="720" height="10" fill="#c8b8ad" transform="rotate(-1 840 1069)"/>
</svg>
<div class="abs" style="left:120px;top:1038px;width:200px;height:200px;border-radius:50%;background:rgba(255,255,255,.18);display:flex;align-items:center;justify-content:center;font-weight:700;font-size:34px;line-height:1.05;color:rgba(255,255,255,.35);text-align:center">Kestrel<br>Way</div>

<h2 class="services-title">Our SERVICES</h2>

<div class="service" style="left:149px;top:1364px">
  <div class="service-ring tone-neuro" role="img" aria-label="Neuromuscular therapy illustration of hands on a shoulder"><i></i></div>
  <div class="service-label" style="top:82px">Neuromuscular</div>
</div>
<div class="service" style="left:327px;top:1307px">
  <div class="service-ring tone-myo" role="img" aria-label="Myofascial release illustration of hands on an upper back"><i></i></div>
  <div class="service-label" style="top:86px">Myofascial<br>Release</div>
</div>
<div class="service" style="left:503px;top:1364px">
  <div class="service-ring tone-spont" role="img" aria-label="Spontaneous muscle release illustration of a lower back"><i></i></div>
  <div class="service-label" style="top:82px">Spontaneous<br>Muscle Release</div>
</div>
<div class="service" style="left:693px;top:1367px">
  <div class="service-ring tone-postural" role="img" aria-label="Postural restoration illustration of thumbs pressing the spine"><i></i></div>
  <div class="service-label" style="top:-128px">Postural<br>Restoration</div>
</div>
<div class="service" style="left:871px;top:1426px">
  <div class="service-ring tone-ortho" role="img" aria-label="Orthopedic massage illustration of a knee joint"><i></i></div>
  <div class="service-label" style="top:-112px">Orthopedic</div>
</div>
<div class="service" style="left:1047px;top:1367px">
  <div class="service-ring tone-medical" role="img" aria-label="Medical massage illustration of a spine"><i></i></div>
  <div class="service-label" style="top:-128px">Medical<br>Massage</div>
</div>

<section class="reviews">
  <div class="photo" role="img" aria-label="Relaxed client lying on a massage table" style="inset:0;background:linear-gradient(90deg,rgba(0,0,0,.25),rgba(120,110,100,.15),rgba(0,0,0,.3))"></div>
  <h2><em>5/5 STARS</em> Massage Therapy</h2>
  <svg class="stars" width="88" height="20" viewBox="0 0 88 20" aria-label="Five stars">
    <g fill="#f0a81c">
      <polygon points="9,1 11.5,7 18,7.3 13,11.5 14.6,18 9,14.4 3.4,18 5,11.5 0,7.3 6.5,7"/>
      <polygon transform="translate(17.5 0)" points="9,1 11.5,7 18,7.3 13,11.5 14.6,18 9,14.4 3.4,18 5,11.5 0,7.3 6.5,7"/>
      <polygon transform="translate(35 0)" points="9,1 11.5,7 18,7.3 13,11.5 14.6,18 9,14.4 3.4,18 5,11.5 0,7.3 6.5,7"/>
      <polygon transform="translate(52.5 0)" points="9,1 11.5,7 18,7.3 13,11.5 14.6,18 9,14.4 3.4,18 5,11.5 0,7.3 6.5,7"/>
      <polygon transform="translate(70 0)" points="9,1 11.5,7 18,7.3 13,11.5 14.6,18 9,14.4 3.4,18 5,11.5 0,7.3 6.5,7"/>
    </g>
  </svg>
  <svg class="arrow" style="left:389px" width="18" height="16" viewBox="0 0 18 16" aria-label="Previous"><polygon points="0,8 9,0 9,5 18,5 18,11 9,11 9,16" fill="var(--white)"/></svg>
  <svg class="arrow" style="left:793px" width="18" height="16" viewBox="0 0 18 16" aria-label="Next"><polygon points="18,8 9,0 9,5 0,5 0,11 9,11 9,16" fill="var(--teal)"/></svg>
  <div class="avatar" role="img" aria-label="Portrait of reviewer Darcy T."></div>
  <div class="reviewer">Darcy T.</div>
  <div class="review-date">December 17, 2015</div>
  <p class="quote">Lina and Paul at Kestrel Way are awesome! I recently had open heart surgery, and Lina worked on me to increase my range of motion while helping with the pinched nerve from my arm being in the same position for so long during my surgery.</p>
</section>

<section class="call">
  <div class="call-number">(206) 555-0148</div>
  <div class="btn-outline call-btn">CALL NOW</div>
</section>
<div class="device" role="img" aria-label="Smartphone lying at an angle showing the mobile site"></div>

<footer class="footer">
  <div class="photo" role="img" aria-label="Stacked spa stones with a pink orchid" style="left:0;top:-12px;width:240px;height:272px;background:linear-gradient(160deg,#6d6d6d 0%,#4a4a4a 45%,#b14f9c 75%,#4f7a2c 100%)"></div>
  <div class="photo" role="img" aria-label="Painted wooden sign on a white building with climbing plants" style="left:0;top:268px;width:626px;height:253px;background:linear-gradient(120deg,#3f5e2a 0%,#c9c2b3 35%,#e9e6df 60%,#8d7b64 100%)"></div>

  <div class="contact-line" style="top:57px">
    <svg width="18" height="20" viewBox="0 0 18 20" aria-hidden="true"><path d="M9 1v18M3 4h12l2 2-2 2H3M15 11H3l-2 2 2 2h12" fill="none" stroke="#e6e6e6" stroke-width="1.6"/></svg>
    Alderbrook, Washington 98190</div>
  <div class="contact-line" style="top:93px">
    <svg width="18" height="18" viewBox="0 0 18 18" aria-hidden="true"><path d="M4 1l3 4-2 2c1 2 3 4 5 5l2-2 4 3-2 3C8 16 2 10 1 4z" fill="none" stroke="#e6e6e6" stroke-width="1.4"/></svg>
    (206) 555-0148</div>
  <div class="contact-line" style="top:128px">
    <svg width="18" height="14" viewBox="0 0 18 14" aria-hidden="true"><rect x="1" y="1" width="16" height="12" fill="none" stroke="#e6e6e6" stroke-width="1.4"/><path d="M1 1l8 7 8-7" fill="none" stroke="#e6e6e6" stroke-width="1.4"/></svg>
    kestrelwaymassage@fernmail.net</div>
  <div class="contact-title">CONTACT US</div>

  <div class="field" style="top:53px;height:50px">Name</div>
  <div class="field" style="top:115px;height:50px">E-Mail</div>
  <div class="field" style="top:178px;height:153px">Message</div>
  <div class="send">SEND</div>

  <div class="footer-brand">Kestrel<br>Way</div>
  <div class="social filled" style="left:932px" aria-label="Social link"></div>
  <div class="social" style="left:994px" aria-label="Social link"></div>
  <div class="social" style="left:1056px" aria-label="Social link"></div>

  <div class="copyright">©2015 <span>KESTREL WAY</span>. All Rights Reserved</div>
</footer>

</body>
</html>
```